Business Card Design

We need a business card designed for our new company. Prefer a black card with white logo & writing.

Contact Information for Business Card

Ted Galloway, address: 7-4812 Fernhollow Road, Abbotsford, BC, V3K 8R2, Office Phone: 604-712-3390, Cell: 604-947-2164, Email: ted@resinworkshub.ca

Colors

Designer to choose only greyscale colors for use in the design.

```html
<!DOCTYPE html>
<html lang="en">
<head>
<meta charset="utf-8">
<title>Resin Works Hub – Business Card</title>
<link rel="stylesheet" href="https://fonts.googleapis.com/css2?family=Montserrat:wght@400;700;800&display=swap">
<style>
  :root {
    --canvas: #3a3633;
    --card: #1c1c1c;
    --ink: #ffffff;
    --ink-soft: #e4e4e4;
    --rule: #bdbdbd;
  }
  * { box-sizing: border-box; margin: 0; padding: 0; }
  html, body { width: 1200px; height: 786px; overflow: hidden; }
  body {
    background: var(--canvas);
    font-family: "Montserrat", sans-serif;
    color: var(--ink);
    position: relative;
  }
  .card {
    position: absolute;
    top: 245px;
    width: 520px;
    height: 296px;
    background: var(--card);
    border-radius: 2px;
  }
  .card--back { left: 55px; }
  .card--front { left: 625px; display: flex; align-items: center; justify-content: center; }

  .brand {
    display: flex;
    align-items: center;
    gap: 10px;
    font-weight: 800;
    color: var(--ink);
    text-transform: uppercase;
    line-height: 1;
  }
  .brand__mark { background: var(--ink); flex: none; }
  .brand__name { display: flex; flex-direction: column; }

  .card--front .brand { font-size: 40px; gap: 16px; }
  .card--front .brand__mark { width: 26px; height: 26px; }

  .card--back .brand {
    position: absolute;
    left: 32px;
    top: 50%;
    transform: translateY(-50%);
    font-size: 25px;
  }
  .card--back .brand__mark { width: 16px; height: 16px; }

  .divider {
    position: absolute;
    left: 262px;
    top: 62px;
    width: 1px;
    height: 172px;
    background: var(--rule);
  }
  .contact {
    position: absolute;
    left: 292px;
    top: 66px;
    font-size: 13.5px;
    color: var(--ink-soft);
    line-height: 1.5;
  }
  .contact__name {
    font-size: 20px;
    font-weight: 700;
    color: var(--ink);
    margin-bottom: 10px;
  }
  .contact__list { list-style: none; }
  .contact__item { display: flex; align-items: center; gap: 7px; }
  .contact__item svg { width: 11px; height: 11px; fill: var(--ink-soft); flex: none; }
  .contact__address { margin-top: 14px; }
</style>
</head>
<body>
  <section class="card card--back" aria-label="Card back with contact details">
    <div class="brand">
      <span class="brand__mark"></span>
      <span class="brand__name"><span>Resin</span><span>Works Hub</span></span>
    </div>
    <div class="divider"></div>
    <div class="contact">
      <h1 class="contact__name">Ted Galloway</h1>
      <ul class="contact__list">
        <li class="contact__item">
          <svg viewBox="0 0 24 24" aria-hidden="true"><path d="M6.6 10.8a15.1 15.1 0 0 0 6.6 6.6l2.2-2.2a1 1 0 0 1 1-.25 11.4 11.4 0 0 0 3.6.57 1 1 0 0 1 1 1V20a1 1 0 0 1-1 1A17 17 0 0 1 3 4a1 1 0 0 1 1-1h3.5a1 1 0 0 1 1 1c0 1.25.2 2.45.57 3.57a1 1 0 0 1-.25 1z"/></svg>
          604-712-3390
        </li>
        <li class="contact__item">
          <svg viewBox="0 0 24 24" aria-hidden="true"><path d="M7 1h10a2 2 0 0 1 2 2v18a2 2 0 0 1-2 2H7a2 2 0 0 1-2-2V3a2 2 0 0 1 2-2zm0 3v14h10V4zm5 15.5a1.2 1.2 0 1 0 0 2.4 1.2 1.2 0 0 0 0-2.4z"/></svg>
          604-947-2164
        </li>
        <li class="contact__item">
          <svg viewBox="0 0 24 24" aria-hidden="true"><path d="M3 5h18a1 1 0 0 1 1 1v12a1 1 0 0 1-1 1H3a1 1 0 0 1-1-1V6a1 1 0 0 1 1-1zm9 7.5L4 7.3V17h16V7.3z"/></svg>
          ted@resinworkshub.ca
        </li>
      </ul>
      <p class="contact__address">7-4812 Fernhollow Road,<br>Abbotsford, BC, V3K 8R2</p>
    </div>
  </section>

  <section class="card card--front" aria-label="Card front">
    <div class="brand">
      <span class="brand__mark"></span>
      <span class="brand__name"><span>Resin</span><span>Works Hub</span></span>
    </div>
  </section>
</body>
</html>
```